Retail Jewelry Business Card Design Project

We are in need of a new business card design for a retail jewelry store. This store is in the business of fine jewelry including but not specific to bridal jewelry, diamonds, designer jewelry and watches.

This store has been in business for 20 years but continues to strive for a modern professional appeal. The main colors use for this business are a royal blue, white and silver.

Target Market(s)

Target market is ages 18-50

Industry/Entity Type

Jewelry

Requirements
Must have
• Sales Person Name
Sales Person Email Address

Store Address
Store Phone
Website

Standard business card size. No odd shapes or sizes.
Nice to have
• Overall modern feel for card.

We have thought that a design with a nice feature of the logo on the back of the card would be nice but open to ideas.
Should not have
• No specific images of jewelry should be used.

```html
<!DOCTYPE html>
<html lang="en">
<head>
<meta charset="utf-8">
<title>Marcus Hale Fine Jewelry – Business Card Concepts</title>
<link rel="stylesheet" href="https://fonts.googleapis.com/css2?family=Source+Sans+3:ital,wght@0,400;0,600;1,700&display=swap">
<style>
  :root {
    --royal: #2e3192;
    --lavender: #7571b3;
    --white: #ffffff;
    --ink: #1d1d1d;
    --text-grey: #3a3a3a;
    --backdrop: #e8e5e1;
    --card-radius: 22px;
  }
  * { margin: 0; padding: 0; box-sizing: border-box; }
  html, body { width: 1200px; height: 788px; overflow: hidden; }
  body {
    position: relative;
    background: var(--backdrop);
    font-family: "Source Sans 3", sans-serif;
  }
  .view-label {
    position: absolute;
    width: 525px;
    text-align: center;
    font-size: 22px;
    color: var(--ink);
  }
  .card {
    position: absolute;
    width: 525px;
    height: 300px;
    border-radius: var(--card-radius);
    overflow: hidden;
    box-shadow: 0 4px 10px rgba(0,0,0,.25);
  }
  .card--white { background: var(--white); }
  .card--royal { background: var(--royal); }
  .card--lavender { background: var(--lavender); }

  .wordmark {
    position: absolute;
    left: 0; right: 0;
    text-align: center;
    font-weight: 600;
    line-height: 1.1;
    color: var(--royal);
  }
  .card--royal .wordmark { color: var(--white); }
  .wordmark--front { top: 38px; font-size: 30px; }
  .wordmark--back { top: 80px; font-size: 44px; }

  .website-line {
    position: absolute;
    left: 0; right: 0;
    bottom: 24px;
    text-align: center;
    font-size: 13px;
    letter-spacing: 2px;
    color: var(--royal);
  }
  .card--royal .website-line { color: var(--white); }
  .card--lavender .website-line { color: var(--ink); }

  .person-name {
    position: absolute;
    top: 145px; left: 0; right: 0;
    text-align: center;
    font-size: 17px;
    color: var(--royal);
  }
  .contact-lines {
    position: absolute;
    top: 181px; left: 0; right: 0;
    text-align: center;
    font-size: 13px;
    line-height: 19px;
    color: var(--text-grey);
  }
  .contact-lines em { font-weight: 700; }
  .ribbons { position: absolute; left: 0; top: 0; }
  .ribbon-text {
    position: absolute;
    font-size: 13px;
    color: var(--white);
  }
  .ribbon-text--email { left: 42px; top: 237px; }
  .ribbon-text--web { left: 327px; top: 254px; }
</style>
</head>
<body>
  <div class="view-label" style="left:55px;top:33px;">Front</div>
  <div class="view-label" style="left:621px;top:33px;">Back - 1</div>
  <div class="view-label" style="left:55px;top:404px;">Back - 2</div>
  <div class="view-label" style="left:621px;top:404px;">Back - 3</div>

  <section class="card card--white" style="left:55px;top:73px;">
    <div class="wordmark wordmark--front">Marcus Hale<br>Fine Jewelry</div>
    <div class="person-name">Marcus Hale Brennan</div>
    <div class="contact-lines">
      <em>phone</em> : 123-555-0188<br>
      2280 Linden Street, Bay Harbor, FL 32405
    </div>
    <svg class="ribbons" width="525" height="300" viewBox="0 0 525 300">
      <polygon points="243,245 525,245 525,282 243,282 270,262" fill="var(--lavender)" />
      <polygon points="0,227 307,227 268,263 0,263" fill="var(--royal)" />
    </svg>
    <div class="ribbon-text ribbon-text--email">marcus@marcushalejewelry.com</div>
    <div class="ribbon-text ribbon-text--web">www.marcushalejewelry.com</div>
  </section>

  <section class="card card--white" style="left:621px;top:73px;">
    <div class="wordmark wordmark--back">Marcus Hale<br>Fine Jewelry</div>
    <div class="website-line">www.marcushalejewelry.com</div>
  </section>

  <section class="card card--royal" style="left:55px;top:445px;">
    <div class="wordmark wordmark--back">Marcus Hale<br>Fine Jewelry</div>
    <div class="website-line">www.marcushalejewelry.com</div>
  </section>

  <section class="card card--lavender" style="left:621px;top:445px;">
    <div class="wordmark wordmark--back">Marcus Hale<br>Fine Jewelry</div>
    <div class="website-line">www.marcushalejewelry.com</div>
  </section>
</body>
</html>
```